Business Card Design

We would like to re-design our business cards. Our Company - Qwinrel Turbochargers, rebuilds turbochargers and sells replacement parts. Our website is: http://www.qwinrelturbochargers-example.com
We just had our logo changed. I will attach the file. Looking for fresh new/modern business card. We like the colors red, black, white and silver. Black background looks attractive, but not a requirement. The final design should communicate reasonable/competitive prices, top quality and reliability of our products.
Updates
Project Deadline Extended
Reason: Need to finalize the info on the card. Currently working on changing address and email info. Want to make sure it is the correct one before accepting the final design. Unless, this is something that can be changed at a later time..??
Industry/Entity Type
Business
Contact Information for Business Card
QWINREL TURBOCHARGERS, LLC
20473 Harwick Lane NE
Massillon, OH 44647
Tel: +1-555-214-7390
Fax: +1-555-267-1842
info@QwinrelTurbochargers-example.com
Our current business card had the following highlights:
*We rebuild all Turbocharges for Automotive, Diesel and Industrial
*Precision Balancing and in-house turbocharger needs
*All Turbocharger replacement parts are made in USA / U.K.
Look and feel
Each slider illustrates characteristics of the customer's brand and the style your logo design should communicate.

```html
<!DOCTYPE html>
<html lang="en">
<head>
<meta charset="utf-8">
<title>Qwinrel Turbochargers – Business Cards</title>
<link href="https://fonts.googleapis.com/css2?family=Montserrat:wght@400;500;700;800&display=swap" rel="stylesheet">
<style>
  :root {
    --bg: #dcdcdc;
    --card: #ffffff;
    --panel: #f6f6f6;
    --red: #e1251b;
    --red-dark: #c81d14;
    --black: #141414;
    --ink: #2a2a2a;
    --muted: #555555;
    --line: #ececec;
  }
  * { box-sizing: border-box; margin: 0; padding: 0; }
  html, body {
    width: 1200px; height: 852px; overflow: hidden;
    background: var(--bg);
    font-family: "Montserrat", Arial, sans-serif;
  }
  .stage { position: relative; width: 1200px; height: 852px; }

  .card {
    position: absolute;
    width: 520px; height: 297px;
    background: var(--card);
    border-radius: 22px;
    overflow: hidden;
    box-shadow: 0 10px 24px rgba(0,0,0,.18);
  }

  /* Front */
  .card-front { left: 80px; top: 110px; }
  .card-front .sheen {
    position: absolute; right: 0; top: 0; width: 260px; height: 100%;
    background: linear-gradient(120deg, rgba(0,0,0,0) 20%, rgba(0,0,0,.035) 50%, rgba(0,0,0,0) 80%);
  }
  .brand {
    display: flex; align-items: center; gap: 10px;
    font-weight: 800; color: var(--black); letter-spacing: .2px;
  }
  .brand .mark { width: 18px; height: 18px; background: var(--red); flex: none; }
  .card-front .brand {
    position: absolute; left: 0; right: 0; top: 108px;
    justify-content: center; font-size: 30px;
  }
  .card-front .web-row {
    position: absolute; left: 0; right: 0; bottom: 48px;
    display: flex; align-items: center; justify-content: center; gap: 16px;
    font-size: 13px; color: var(--ink); font-weight: 500;
    white-space: nowrap;
  }
  .card-front .rule { width: 70px; height: 2px; background: var(--red); }

  /* Back */
  .card-back { left: 600px; top: 445px; }
  .card-back .info-panel {
    position: absolute; left: 250px; top: 0; right: 0; height: 227px;
    background: var(--panel);
    border-left: 1px solid var(--line);
  }
  .card-back .brand {
    position: absolute; left: 26px; top: 96px;
    flex-direction: column; align-items: flex-start; gap: 6px;
    font-size: 26px; line-height: 1;
  }
  .card-back .brand .mark { width: 16px; height: 16px; }
  .person { position: absolute; left: 272px; top: 30px; }
  .person-name { color: var(--red); font-weight: 700; font-size: 17px; }
  .person-title { color: var(--muted); font-size: 10.5px; margin-top: 4px; }
  .contacts {
    position: absolute; left: 272px; top: 100px;
    list-style: none; font-size: 10.5px; color: var(--ink); line-height: 1.55;
    white-space: nowrap;
  }
  .contacts li { display: flex; align-items: flex-start; gap: 7px; }
  .contacts svg { width: 10px; height: 10px; margin-top: 3px; flex: none; fill: var(--red); }
  .contacts .indent { padding-left: 17px; }
  .band-red {
    position: absolute; left: 0; bottom: 0; width: 290px; height: 26px;
    background: linear-gradient(180deg, var(--red), var(--red-dark));
  }
  .band-black {
    position: absolute; right: 0; bottom: 0; width: 290px; height: 70px;
    background: var(--black);
    clip-path: polygon(12% 0, 100% 0, 100% 100%, 0 100%);
    display: flex; align-items: center; justify-content: flex-end;
    padding-right: 18px;
    color: #fff; font-size: 10px; font-weight: 500;
    white-space: nowrap;
  }
</style>
</head>
<body>
<main class="stage">

  <section class="card card-front" aria-label="Business card front">
    <div class="sheen"></div>
    <div class="brand"><span class="mark"></span>Qwinrel Turbochargers</div>
    <div class="web-row">
      <span class="rule"></span>
      <span>www.QwinrelTurbochargers-example.com</span>
      <span class="rule"></span>
    </div>
  </section>

  <section class="card card-back" aria-label="Business card back">
    <div class="info-panel"></div>
    <div class="brand"><span class="mark"></span>Qwinrel<br>Turbochargers</div>

    <div class="person">
      <p class="person-name">Your Long Name</p>
      <p class="person-title">Managing Director</p>
    </div>

    <ul class="contacts">
      <li>
        <svg viewBox="0 0 10 10"><path d="M1 3c0-1 1-2 2-2h4c1 0 2 1 2 2v1H7V3H3v1H1zM2 5h6l1 4H1z"/></svg>
        1.555.214.7390
      </li>
      <li>
        <svg viewBox="0 0 10 10"><path d="M0 2h10v6H0zM0 2l5 3.5L10 2v1L5 6.5 0 3z"/></svg>
        info@QwinrelTurbochargers-example.com
      </li>
      <li>
        <svg viewBox="0 0 10 10"><path d="M5 0a3.5 3.5 0 0 1 3.5 3.5C8.5 6 5 10 5 10S1.5 6 1.5 3.5A3.5 3.5 0 0 1 5 0zm0 2a1.5 1.5 0 1 0 0 3 1.5 1.5 0 0 0 0-3z"/></svg>
        5812 Brindle Ave. NW
      </li>
      <li class="indent">North Ashford, Ohio</li>
    </ul>

    <div class="band-red"></div>
    <div class="band-black">www.QwinrelTurbochargers-example.com</div>
  </section>

</main>
</body>
</html>
```